HOT TUB - SPAS service needs an business card

I need an business for my company who his specialise in a maintenance,water treatment and cleaning of Hot Tub - Spas for commercial and residential customers. The company operate mainly in the ski resort of Chamonix, Megève and St Gervais. The final product should communicate pure water, cleanest and professional for luxury property's.
I have upload a logo but any improvement on it is welcome.(color,size, details etc..) or any other idea. Thank you
Company Name: 58 BAINS
My name: Lucien Marchetti
Email: lucimarch@examplemail.net
Tel: +33 (0)6 71 58 29 64
Description to be on the card in french(first langage) and in English:
- Spas service
- Entretien, traitement eau, nettoyage.
- Maintenance, water treatment, cleaning.
Industry/Entity Type
Residential
Colors
Designer to choose colors to be used in the design.
Look and feel
Each slider illustrates characteristics of the customer's brand and the style your logo design should communicate.

```html
<!DOCTYPE html>
<html lang="fr">
<head>
<meta charset="utf-8">
<title>58 BAINS – Business Card</title>
<link rel="stylesheet" href="https://fonts.googleapis.com/css2?family=Source+Sans+3:wght@400;600;700&display=swap">
<style>
  :root {
    --page-bg: #e9edf1;
    --water-light: #4fb0f2;
    --water-mid: #2e96ea;
    --water-deep: #1a82dc;
    --wave-deep: #1777d6;
    --wave-cyan: #22c4f2;
    --wave-pale: #5fd2f7;
    --ink: #ffffff;
    --card-shadow: rgba(20, 40, 70, 0.28);
  }
  * { box-sizing: border-box; margin: 0; padding: 0; }
  html, body {
    width: 1200px; height: 1100px; overflow: hidden;
    background: var(--page-bg);
    font-family: "Source Sans 3", "Myriad Pro", Arial, sans-serif;
    color: var(--ink);
  }
  .canvas { position: relative; width: 1200px; height: 1100px; }

  .card {
    position: absolute;
    width: 862px; height: 492px;
    overflow: hidden;
    box-shadow: 0 6px 18px var(--card-shadow);
  }
  .card--front { left: 61px; top: 31px; }
  .card--back  { left: 279px; top: 552px; }

  .droplet-field {
    position: absolute; inset: 0;
    background:
      radial-gradient(ellipse at 30% 20%, rgba(255,255,255,0.16), transparent 60%),
      radial-gradient(ellipse at 80% 70%, rgba(0,60,140,0.14), transparent 65%),
      linear-gradient(160deg, var(--water-light) 0%, var(--water-mid) 55%, var(--water-deep) 100%);
  }

  .wave { position: absolute; inset: 0; width: 862px; height: 492px; }

  .brand-mark {
    position: absolute;
    font-weight: 600;
    letter-spacing: 0.06em;
    color: var(--ink);
  }
  .card--front .brand-mark { left: 77px; top: 58px; font-size: 60px; line-height: 1; }

  .company-name {
    position: absolute; left: 87px; top: 204px;
    font-size: 39px; font-weight: 600; line-height: 1;
  }
  .contact-list { position: absolute; left: 80px; top: 290px; list-style: none; }
  .contact-item {
    display: flex; align-items: center; gap: 12px;
    font-size: 25px; line-height: 1; height: 32px; margin-bottom: 20px;
  }
  .contact-icon { width: 24px; height: 24px; flex: none; }
  .owner-name {
    position: absolute; right: 18px; top: 421px;
    font-size: 29px; font-weight: 700; line-height: 1;
  }

  .card--back .brand-mark {
    left: 0; right: 0; top: 140px; text-align: center;
    font-size: 76px; line-height: 1;
  }
  .services { position: absolute; left: 0; right: 0; top: 344px; text-align: center; }
  .services-title { font-size: 29px; font-weight: 700; line-height: 1; margin-bottom: 16px; }
  .services-line { font-size: 29px; line-height: 1; margin-bottom: 12px; white-space: nowrap; }
</style>
</head>
<body>
<main class="canvas">

  <section class="card card--front">
    <div class="droplet-field" role="img" aria-label="Close-up photo of water droplets on a blue surface"></div>
    <svg class="wave" viewBox="0 0 862 492" aria-hidden="true">
      <path d="M0 400 C210 500 430 470 610 370 C710 315 800 285 862 262 L862 492 L0 492 Z" fill="var(--wave-deep)"/>
      <path d="M0 424 C210 515 440 478 620 385 C720 333 805 300 862 286 L862 300 C805 316 725 350 630 400 C440 498 200 520 0 446 Z" fill="var(--wave-pale)" opacity="0.85"/>
      <path d="M0 455 C200 530 450 500 640 405 C735 357 810 325 862 314 L862 332 C810 345 740 376 650 420 C450 518 190 532 0 476 Z" fill="var(--wave-cyan)"/>
    </svg>
    <div class="brand-mark">58 BAINS</div>
    <h1 class="company-name">58 BAINS</h1>
    <ul class="contact-list">
      <li class="contact-item">
        <svg class="contact-icon" viewBox="0 0 24 24" aria-hidden="true">
          <path d="M6.6 3.5l3 3.2-1.8 2.4c1 2.2 2.9 4.1 5.1 5.1l2.4-1.8 3.2 3-1.9 3.1C10.4 19 5 13.6 3.5 5.4z" fill="var(--ink)"/>
        </svg>
        <span>+33 (0)6 71 58 29 64</span>
      </li>
      <li class="contact-item">
        <svg class="contact-icon" viewBox="0 0 24 24" aria-hidden="true">
          <path d="M2 9 L12 3 L22 9 V20 H2 Z" fill="var(--ink)"/>
          <path d="M2 9 L12 15 L22 9" fill="none" stroke="var(--water-mid)" stroke-width="1.6"/>
        </svg>
        <span>lucimarch@examplemail.net</span>
      </li>
    </ul>
    <p class="owner-name">Lucien Marchetti</p>
  </section>

  <section class="card card--back">
    <div class="droplet-field" role="img" aria-label="Close-up photo of water droplets on a blue surface"></div>
    <div class="brand-mark">58 BAINS</div>
    <div class="services">
      <h2 class="services-title">SPAS SERVICES</h2>
      <p class="services-line">•Entretien &nbsp;•traitement eau &nbsp;•nettoyage</p>
      <p class="services-line">•Maintenance &nbsp;•water treatment &nbsp;•cleaning.</p>
    </div>
  </section>

</main>
</body>
</html>
```